Copperleaf Roofing Business Card

This is my current business card. But I’d like to make some changes. Somewhere on the card I’d like to list some of the services we offer. Maybe on the back? But I’d still like to keep the red. White and black modern look.

-residential & commercial roofing
-Roof Repairs & Maintenance
-Storm Damage & Insurance Claims specialist
-Christmas Lights and permanent Christmas lights
Fencing. Windows. Gutters. Siding. Sheetrock, painting.

```html
<!DOCTYPE html>
<html lang="en">
<head>
<meta charset="utf-8">
<title>Copperleaf Roofing Business Card</title>
<link href="https://fonts.googleapis.com/css2?family=Orbitron:wght@800&family=Open+Sans:wght@400;600&family=Fira+Sans+Condensed:wght@400;500&display=swap" rel="stylesheet">
<style>
  :root {
    --bg: #d4d5d7;
    --card-black: #121212;
    --red: #e02127;
    --red-mid: #b3141a;
    --red-dark: #6e0e10;
    --black: #0a0a0a;
    --white: #ffffff;
  }
  * { margin: 0; padding: 0; box-sizing: border-box; }
  html, body { width: 900px; height: 1200px; overflow: hidden; }
  body { background: var(--bg); position: relative; font-family: "Open Sans", sans-serif; }

  .card {
    position: absolute; left: 136px; width: 630px; height: 357px;
    border-radius: 12px; overflow: hidden;
    box-shadow: 4px 6px 10px rgba(0,0,0,0.35);
  }
  .card--front { top: 215px; }
  .card--back { top: 628px; height: 359px; background: var(--card-black); }

  .pattern-area {
    position: absolute; inset: 0;
    background: linear-gradient(180deg, var(--red-dark) 0%, var(--red-mid) 30%, var(--black) 55%, var(--red-mid) 75%, var(--red-dark) 100%);
  }

  .brand {
    position: absolute; left: 0; right: 0; top: 228px;
    text-align: center; font-family: "Orbitron", sans-serif; font-weight: 800;
    color: var(--white); line-height: 1.2;
  }
  .brand__name { font-size: 30px; letter-spacing: 0.5px; }
  .brand__sub { font-size: 22px; letter-spacing: 1px; margin-top: 2px; }

  .person { position: absolute; left: 60px; top: 100px; width: 232px; text-align: right; }
  .person__name { font-family: "Orbitron", sans-serif; font-weight: 800; font-size: 20px; color: var(--white); white-space: nowrap; }
  .person__name .first { color: var(--red); }
  .person__role { font-size: 14px; color: var(--red); letter-spacing: .5px; margin-top: 4px; }

  .divider-v { position: absolute; left: 314px; top: 88px; width: 1.5px; height: 68px; background: var(--white); }

  .contact { position: absolute; left: 336px; top: 86px; list-style: none; }
  .contact li { display: flex; align-items: center; gap: 6px; height: 25px; color: var(--white); font-size: 15px; letter-spacing: 1.2px; }
  .contact svg { width: 14px; height: 14px; fill: var(--red); flex: none; }

  .services { position: absolute; left: 0; right: 0; top: 202px; text-align: center; }
  .services__title {
    display: flex; align-items: center; justify-content: center; gap: 18px;
    font-family: "Fira Sans Condensed", sans-serif; font-weight: 500;
    color: var(--red); font-size: 20px; letter-spacing: .5px;
  }
  .services__title::before, .services__title::after { content: ""; width: 135px; height: 1px; background: var(--white); }
  .services__list { list-style: none; margin-top: 8px; font-family: "Fira Sans Condensed", sans-serif; color: var(--white); font-size: 14.5px; line-height: 25px; }
  .sep { color: var(--red); padding: 0 3px; }

  .strip {
    position: absolute; left: 0; right: 0; bottom: 0; height: 12px;
    background: linear-gradient(90deg, var(--red-dark), var(--red-mid) 50%, var(--red-dark));
  }
</style>
</head>
<body>
  <section class="card card--front">
    <div class="pattern-area" role="img" aria-label="Red, white and black tartan plaid pattern"></div>
    <div class="brand">
      <div class="brand__name">COPPERLEAF</div>
      <div class="brand__sub">ROOFING CO.</div>
    </div>
  </section>

  <section class="card card--back">
    <div class="person">
      <div class="person__name"><span class="first">DALE</span> MERCER</div>
      <div class="person__role">OWNER</div>
    </div>
    <div class="divider-v"></div>
    <ul class="contact">
      <li><svg viewBox="0 0 24 24"><path d="M6.6 10.8a15.1 15.1 0 0 0 6.6 6.6l2.2-2.2c.3-.3.7-.4 1-.2 1.1.4 2.3.6 3.6.6.6 0 1 .4 1 1V20c0 .6-.4 1-1 1A17 17 0 0 1 3 4c0-.6.4-1 1-1h3.5c.6 0 1 .4 1 1 0 1.3.2 2.5.6 3.6.1.3 0 .7-.2 1z"/></svg>555-014-2290</li>
      <li><svg viewBox="0 0 24 24"><path d="M2 5h20v14H2zm2 2v.5l8 5 8-5V7l-8 5z"/></svg>dale@copperleafroofing.co</li>
      <li><svg viewBox="0 0 24 24"><path d="M12 2a10 10 0 1 0 0 20 10 10 0 0 0 0-20zm-1 2.1V8H7.4A8 8 0 0 1 11 4.1zM13 4.1A8 8 0 0 1 16.6 8H13zM4.3 10H11v4H4.3a8 8 0 0 1 0-4zm8.7 0h6.7a8 8 0 0 1 0 4H13zM7.4 16H11v3.9A8 8 0 0 1 7.4 16zm5.6 0h3.6a8 8 0 0 1-3.6 3.9z"/></svg>www.copperleafroofing.co</li>
    </ul>

    <div class="services">
      <h2 class="services__title">SERVICES WE OFFER</h2>
      <ul class="services__list">
        <li>Residential &amp; Commercial Roofing <span class="sep">|</span> Roof Repairs &amp; Maintenance</li>
        <li>Storm Damage &amp; Insurance Claims specialist <span class="sep">|</span> Christmas Lights and permanent Christmas lights</li>
        <li>Fencing <span class="sep">|</span> Windows <span class="sep">|</span> Gutters <span class="sep">|</span> Siding <span class="sep">|</span> Sheetrock <span class="sep">|</span> Painting.</li>
      </ul>
    </div>

    <div class="strip" role="img" aria-label="Thin band of red, white and black tartan plaid"></div>
  </section>
</body>
</html>
```